Marlo K Dress Designs

My company (MarloK) designs and creates ladies fashion garments. I am a one person company at the moment with plans to bring on additional staff as the workload increases. At this stage I would prefer to focus on developing regional clients around Wellington, New Zealand so I can personalise the service. Expansion beyond the Wellington region is a dream in the future if all goes well with the website and the business.

I love working with people to create fashion garments for them that showcase their personalities and beauty, whatever their body type or physical appearance. I love helping my clients select the best designs, fabrics, colours and styles to look and feel the very best they can appropriate to the occasion they are dressing for. Sometimes its high-end fashion, sometimes its for daily wearing and on the odd occasion its just to be quirky and have fun with fashion. Clients typically want that special garment or outfit for special occasions like balls, weddings, racedays, reunions, concerts, anniversaries, receptions, functions and formal gatherings.

I have created a range of garments (about 12) which I would like to be showcased on the website. I can reproduce those garment showcased for clients, or I could work with the client to create a special one of a kind outfit for them, or reproduce off an existing dress design, or alter an existing outfit. have a customer focussed industry that focussing on bespoke garments rather than trying to compete with low cost mass produced ladies fashion garment.

I would like to have the prospective clients contact me by email directly from the website and work with them to design, quote, produce and tailor what they want. These fashion garments will be more expensive than off-the-rack garments readily available in shops or online. But they will be specifically tailored for the individuals. Clients will be given a quote based upon the design, type and quantity of the material used before I create the garment.

A couple of quotes in regards to my fashion design that expresses my love for creating and producing great garments for people:
- Percy Haldane - 'You can never be overdressed or overeducated.'
- Pipsy - 'There's no need to dress like everybody else. Its much more fun to create your own.'
- Carlo Benvetti- 'I really want to make clothes that are feminine and help women look beautiful.'

I want to have this website hosted on a server and I want to be able to amend and update the photos and other content myself.

I like a mix of old and new sewing related art/images.

My email address and phone number should be in the contact page. They are shown in the cards below. I will upload photos of my creations soon.

Industry/Entity Type

Fashion

Coding

Coded - Design and coding required

Number of Pages Required

3 page

Colors

Designer to choose colors to be used in the design.

Requirements
Must have
• Blog
• Services (Formal Dresses, Alterations, Buisness attire, every day wear, style consults)
Should not have
• Products

```html
<!DOCTYPE html>
<html lang="en">
<head>
<meta charset="utf-8">
<title>Marlo K Dress Designs</title>
<link href="https://fonts.googleapis.com/css2?family=Playfair+Display:ital,wght@0,400;0,700;1,400&family=Open+Sans:wght@400;600;700&display=swap" rel="stylesheet">
<style>
:root{
  --brand:#b5283f;
  --ink:#222222;
  --text:#555555;
  --muted:#8a8a8a;
  --dark:#262626;
  --darker:#1c1c1c;
  --light:#f1f1f1;
  --white:#ffffff;
}
*{margin:0;padding:0;box-sizing:border-box}
html,body{width:1200px;height:2432px;overflow:hidden}
body{font-family:"Open Sans",Arial,sans-serif;color:var(--text);background:var(--white);position:relative}
.site-header{position:absolute;top:0;left:0;width:1200px;height:150px}
.logo{position:absolute;left:130px;top:20px;font-family:"Playfair Display",Georgia,serif;font-size:62px;color:var(--brand);font-weight:400}
.header-contact{position:absolute;right:130px;top:40px;display:flex;gap:36px;font-size:19px;color:var(--ink);font-weight:600}
.header-contact span{display:flex;align-items:center;gap:8px}
.main-nav{position:absolute;right:130px;top:110px;display:flex;gap:34px;font-size:17px;color:var(--ink)}
.main-nav a{color:inherit;text-decoration:none;padding-bottom:10px}
.main-nav a.active{color:var(--brand);border-bottom:3px solid var(--brand)}
.hero{position:absolute;top:150px;left:0;width:1200px;height:630px;background:linear-gradient(180deg,#d8d6d0 0%,#bdb9b0 45%,#8f8b84 100%)}
.hero-photo{position:absolute;inset:0}
.hero-quote{position:absolute;left:688px;top:238px;width:420px;height:140px;background:rgba(255,255,255,.9);padding:26px 30px;font-family:"Playfair Display",Georgia,serif;font-size:24px;line-height:1.3;color:var(--ink)}
.hero-quote cite{display:block;text-align:right;color:var(--brand);font-style:normal;font-size:22px;margin-top:4px}
.hero-arrow{position:absolute;top:290px;width:24px;height:40px;background:rgba(0,0,0,.35)}
.section-title{font-family:"Playfair Display",Georgia,serif;font-size:46px;font-weight:400;color:var(--brand);line-height:1.2}
.lead{font-size:21px;font-weight:600;line-height:1.3;color:var(--ink);margin-top:14px}
.body-copy{font-size:13px;line-height:1.7;margin-top:18px;color:var(--muted)}
.btn{display:inline-block;margin-top:26px;padding:10px 18px;border:1px solid #bbb;font-size:14px;color:var(--text)}
.welcome{position:absolute;top:780px;left:0;width:1200px;height:440px}
.welcome .copy{position:absolute;left:130px;top:64px;width:430px}
.welcome .photo{position:absolute;left:634px;top:60px;width:436px;height:320px;background:linear-gradient(135deg,#e9e4df,#bfc6d6 60%,#d45b6a)}
.feature{position:absolute;top:1220px;left:0;width:1200px;height:540px;background:var(--dark)}
.feature .photo{position:absolute;left:130px;top:88px;width:438px;height:312px;background:linear-gradient(135deg,#f1ece6,#d8b9a5 55%,#c74b5b)}
.feature .copy{position:absolute;left:600px;top:96px;width:470px}
.feature .section-title{color:var(--white)}
.feature .lead{color:#e6e6e6}
.feature .body-copy{color:#9a9a9a}
.feature .btn{border-color:#666;color:#ccc}
.reviews{position:absolute;top:1760px;left:0;width:1200px;height:452px;text-align:center}
.reviews .section-title{position:absolute;left:0;top:22px;width:1200px}
.review-box{position:absolute;left:192px;top:88px;width:880px;height:200px;background:var(--light);padding:26px 60px;font-family:"Playfair Display",Georgia,serif;font-size:23px;line-height:1.45;color:var(--ink)}
.avatar{position:absolute;left:580px;top:234px;width:104px;height:104px;border-radius:50%;background:linear-gradient(#e8d3c0,#c99b7c);border:4px solid var(--white)}
.reviewer{position:absolute;left:0;top:352px;width:1200px;font-size:14px;color:var(--brand)}
.rev-arrow{position:absolute;top:180px}
.contact-band{position:absolute;top:2212px;left:0;width:1200px;height:108px;background:var(--light);display:flex;justify-content:center;align-items:center;gap:26px;font-size:16px;color:var(--ink)}
.contact-band span{display:flex;align-items:center;gap:8px}
.site-footer{position:absolute;top:2320px;left:0;width:1200px;height:112px;background:var(--darker);color:#8a8a8a;font-size:12px}
.footer-links{position:absolute;left:130px;top:34px;display:flex;gap:20px}
.copyright{position:absolute;left:130px;top:62px}
.social{position:absolute;right:130px;top:38px;display:flex;gap:14px}
.social span{width:20px;height:20px;background:#777}
</style>
</head>
<body>
<header class="site-header">
  <div class="logo">MarloK</div>
  <div class="header-contact">
    <span><svg width="18" height="14" viewBox="0 0 18 14"><rect x="1" y="1" width="16" height="12" fill="none" stroke="#222" stroke-width="2"/><path d="M1 1l8 7 8-7" fill="none" stroke="#222" stroke-width="2"/></svg>marlokdesigner@example.com</span>
    <span><svg width="14" height="16" viewBox="0 0 14 16"><path d="M3 1l3 4-2 2c1 2 3 4 5 5l2-2 3 3-2 2C6 15 0 9 1 3z" fill="#222"/></svg>021 555 014</span>
  </div>
  <nav class="main-nav">
    <a class="active">Home</a><a>Services</a><a>Reviews</a><a>Blog</a><a>About Us</a><a>Contact Us</a>
  </nav>
</header>

<section class="hero">
  <div class="hero-photo" role="img" aria-label="Woman in a long blue gown standing on the steps of a classical columned building"></div>
  <div class="hero-arrow" style="left:0"></div>
  <div class="hero-arrow" style="right:0"></div>
  <blockquote class="hero-quote">“ You can never be overdressed or overeducated .<cite>~ Percy Haldane</cite></blockquote>
</section>

<section class="welcome">
  <div class="copy">
    <h2 class="section-title">Welcome to Marlo K</h2>
    <p class="lead">Vestibulum condimentum, risus ut posuere cursus, velit justo accumsan sem.</p>
    <p class="body-copy">Phasellus consequat sagittis nisi suscipit feugiat. Cras egestas sed nunc hendrerit ultrices ex et nisl. Praesent iaculis faucibus urna sit amet laoreet. Maecenas consequat justo tortor, ut mattis massa imperdiet quis. Fusce eget neque nisi. Sed augue orci elementum in magna congue, tincidunt vulputate eros. Aliquam consectetur orci molestie dictum molestie.</p>
    <span class="btn">Read More</span>
  </div>
  <div class="photo" role="img" aria-label="Overhead view of hands sewing fabric with pins and threads"></div>
</section>

<section class="feature">
  <div class="photo" role="img" aria-label="Hands cutting a paper pattern on fabric at a work table"></div>
  <div class="copy">
    <h2 class="section-title">Aliquam erat</h2>
    <p class="lead">Pellentesque convallis molestie enim amet efficitur lectus sit amet mc pulvinar maximus</p>
    <p class="body-copy">Phasellus consequat sagittis nisi suscipit feugiat. Cras egestas sed nunc hendrerit ultrices ex et nisl. Praesent iaculis faucibus urna sit amet laoreet. Maecenas consequat justo tortor, ut mattis massa imperdiet quis. Fusce eget neque nisi. Sed augue orci elementum in magna congue, tincidunt vulputate eros.</p>
    <span class="btn">Read More</span>
  </div>
</section>

<section class="reviews">
  <h2 class="section-title">Reviews</h2>
  <svg class="rev-arrow" style="left:30px" width="16" height="28" viewBox="0 0 16 28"><path d="M14 2L3 14l11 12" fill="none" stroke="#bbb" stroke-width="3"/></svg>
  <svg class="rev-arrow" style="right:30px" width="16" height="28" viewBox="0 0 16 28"><path d="M2 2l11 12L2 26" fill="none" stroke="#bbb" stroke-width="3"/></svg>
  <div class="review-box">“ Maecenas vel tortor accumsan quam varius imperdiet vel eget elit. Aenean facilisis tincidunt lectus, id dictum nisi luctus eget. Vivamus efficitur ex condimentum, malesuada eros eget, feugiat nibh „</div>
  <div class="avatar" role="img" aria-label="Portrait photo of the reviewer"></div>
  <div class="reviewer">Jane Harlow</div>
</section>

<section class="contact-band">
  <span><svg width="12" height="16" viewBox="0 0 12 16"><path d="M6 0a6 6 0 0 0-6 6c0 4 6 10 6 10s6-6 6-10a6 6 0 0 0-6-6zm0 8a2 2 0 1 1 0-4 2 2 0 0 1 0 4z" fill="#222"/></svg>24 Building name, Street name, City Zipcode</span>
  <span>|</span>
  <span><svg width="14" height="16" viewBox="0 0 14 16"><path d="M3 1l3 4-2 2c1 2 3 4 5 5l2-2 3 3-2 2C6 15 0 9 1 3z" fill="#222"/></svg>Phone : 021 555 014</span>
  <span>|</span>
  <span><svg width="18" height="14" viewBox="0 0 18 14"><rect x="1" y="1" width="16" height="12" fill="none" stroke="#222" stroke-width="2"/><path d="M1 1l8 7 8-7" fill="none" stroke="#222" stroke-width="2"/></svg>Email : marlokdesigner@example.com</span>
</section>

<footer class="site-footer">
  <div class="footer-links"><span>Home</span><span>Services</span><span>Reviews</span><span>Blog</span><span>About Us</span><span>Contact Us</span></div>
  <div class="copyright">Copyright © 2016 Marlo K. All rights reserved.</div>
  <div class="social"><span></span><span></span><span></span></div>
</footer>
</body>
</html>
```